Corporate Template

Looking for a set of corporate slides to be made which contain multiple different slides and orientations. Looking for at least 8 to 10 different master pages plus a Coversheet and closeout page. Incorporating a color palate similar to our logo coloring is preferred.
I have attached a logo.
I like the amber quill works designs best so far. They seem to fit what I'm looking for in terms of visual appearance.
Reason: I'm trying to allow time for a couple new designers to incorporate some changes I requested to their existing designs.

```html
<!DOCTYPE html>
<html lang="en">
<head>
<meta charset="utf-8">
<title>Meridian Neuro-Care — Presentation Template</title>
<link href="https://fonts.googleapis.com/css2?family=Arimo:wght@400;700&display=swap" rel="stylesheet">
<style>
  :root {
    --brand-blue: #2d5fa6;
    --brand-navy: #1f4e8c;
    --glow-blue: #1a90d8;
    --sky-blue: #1a7ec5;
    --leaf-green: #7ab83b;
    --amber: #e0a92b;
    --steel-blue: #4f7fc0;
    --ink: #333333;
    --pale-text: #8fb4e0;
    --row-grey: #dcdcdc;
    --row-light: #f0f0f0;
    --page: #ffffff;
  }
  * { box-sizing: border-box; margin: 0; padding: 0; }
  html, body { width: 1200px; height: 1000px; overflow: hidden; background: var(--page); }
  body { position: relative; font-family: "Arimo", Arial, sans-serif; color: var(--ink); }

  .sheet-title {
    position: absolute; top: 56px; left: 0; width: 1200px; text-align: center;
    font-size: 28px; font-weight: 400; color: var(--brand-navy);
  }

  .slide { position: absolute; width: 335px; height: 255px; overflow: hidden; background: var(--page); }
  .col-1 { left: 25px; } .col-2 { left: 422px; } .col-3 { left: 820px; }
  .row-1 { top: 148px; } .row-2 { top: 430px; } .row-3 { top: 732px; }

  /* Blue feature slides */
  .slide--feature {
    background: radial-gradient(circle at 50% 45%, var(--glow-blue) 0%, #2470bf 22%, var(--brand-blue) 55%);
    color: #fff;
  }
  .dot-field {
    position: absolute; left: 0; top: 0; width: 150px; height: 140px;
    background: radial-gradient(ellipse at 30% 30%, rgba(122,184,59,.45), rgba(224,169,43,.3) 45%, rgba(26,144,216,0) 75%);
  }
  .brand-name { position: absolute; color: #fff; font-weight: 400; line-height: 1; text-transform: uppercase; }
  .brand-name .line-main { display: block; letter-spacing: 1px; }
  .brand-name .line-sub { display: block; letter-spacing: .3px; }

  .cover .brand-name { left: 126px; top: 118px; text-align: left; }
  .cover .line-main { font-size: 24px; }
  .cover .line-sub { font-size: 8.5px; margin-top: 3px; }
  .cover-heading { position: absolute; left: 0; width: 100%; text-align: center; font-size: 14px; }
  .cover-date { position: absolute; left: 0; width: 100%; text-align: center; font-size: 7px; color: var(--pale-text); }

  .section-heading { position: absolute; left: 22px; top: 138px; font-size: 14px; }
  .section-sub { position: absolute; left: 22px; top: 162px; font-size: 8px; color: var(--pale-text); }
  .slide--feature .brand-corner { right: 12px; top: 225px; text-align: right; }
  .brand-corner .line-main { font-size: 14px; }
  .brand-corner .line-sub { font-size: 5.5px; }

  /* Content slides */
  .slide-title {
    position: absolute; left: 34px; top: 18px; font-size: 12.5px; font-weight: 700; color: var(--brand-blue);
  }
  .title-dot { position: absolute; left: 14px; top: 20px; width: 11px; height: 11px; border-radius: 50%; background: var(--glow-blue); }
  .footer-band { position: absolute; left: 0; bottom: 0; width: 100%; height: 19px; background: var(--brand-blue); }
  .footer-band .brand-name { right: 8px; top: 4px; text-align: right; }
  .footer-band .line-main { font-size: 8px; }
  .footer-band .line-sub { font-size: 3.5px; margin-top: 1px; }

  .outline { position: absolute; left: 42px; top: 50px; font-size: 8.5px; list-style: none; line-height: 12px; }
  .outline li::before { content: ""; display: inline-block; margin-right: 4px; }
  .lvl-1::before { content: "•" !important; color: var(--brand-blue); }
  .lvl-2 { padding-left: 6px; } .lvl-2::before { content: "–" !important; }
  .lvl-3 { padding-left: 18px; font-size: 7.5px; } .lvl-3::before { content: "•" !important; font-size: 6px; }
  .lvl-4 { padding-left: 30px; font-size: 7.5px; } .lvl-4::before { content: "–" !important; }
  .lvl-5 { padding-left: 42px; font-size: 7.5px; } .lvl-5::before { content: "»" !important; font-size: 6px; }

  .chart { position: absolute; left: 0; top: 0; width: 335px; height: 255px; font-family: "Arimo", Arial, sans-serif; }

  .data-table { position: absolute; left: 16px; top: 62px; width: 306px; border-collapse: separate; border-spacing: 1px; font-size: 5px; }
  .data-table th { background: var(--brand-blue); color: #fff; font-weight: 700; height: 13px; text-align: center; }
  .data-table th:first-child, .data-table td:first-child { text-align: left; padding-left: 3px; width: 58px; }
  .data-table td { height: 14px; text-align: center; color: #555; }
  .data-table tr:nth-child(odd) td { background: var(--row-grey); }
  .data-table tr:nth-child(even) td { background: var(--row-light); }
</style>
</head>
<body>
  <h1 class="sheet-title">Sample Design 6</h1>

  <!-- Cover -->
  <section class="slide slide--feature cover col-1 row-1">
    <div class="dot-field" role="img" aria-label="Scattered dots in blue, green and amber"></div>
    <div class="brand-name"><span class="line-main">Meridian</span><span class="line-sub">Neuro-Care</span></div>
    <p class="cover-heading" style="top:173px">Presentation Template</p>
    <p class="cover-date" style="top:196px">October 26, 2013</p>
  </section>

  <!-- Section heading -->
  <section class="slide slide--feature col-2 row-1">
    <div class="dot-field" role="img" aria-label="Scattered dots in blue, green and amber"></div>
    <p class="section-heading">Section Heading</p>
    <p class="section-sub">Subheading</p>
    <div class="brand-name brand-corner"><span class="line-main">Meridian</span><span class="line-sub">Neuro-Care</span></div>
  </section>

  <!-- Title and content -->
  <section class="slide col-3 row-1">
    <span class="title-dot"></span>
    <h2 class="slide-title">Title and Content</h2>
    <ul class="outline">
      <li class="lvl-1">Click to edit Master text styles</li>
      <li class="lvl-2">Second level</li>
      <li class="lvl-3">Third level</li>
      <li class="lvl-4">Fourth level</li>
      <li class="lvl-5">Fifth level</li>
    </ul>
    <div class="footer-band"><div class="brand-name"><span class="line-main">Meridian</span><span class="line-sub">Neuro-Care</span></div></div>
  </section>

  <!-- Title only -->
  <section class="slide col-1 row-2">
    <span class="title-dot"></span>
    <h2 class="slide-title">Title Only</h2>
    <div class="footer-band"><div class="brand-name"><span class="line-main">Meridian</span><span class="line-sub">Neuro-Care</span></div></div>
  </section>

  <!-- Pie chart -->
  <section class="slide col-2 row-2">
    <span class="title-dot"></span>
    <h2 class="slide-title">Pie Chart</h2>
    <svg class="chart" viewBox="0 0 335 255">
      <text x="171" y="80" text-anchor="middle" font-size="10" font-weight="700" fill="#222">Chart Title</text>
      <g transform="translate(171,150)">
        <path d="M0,0 L0,-55 A55,55 0 1 1 -26.5,48.2 Z" fill="var(--sky-blue)" stroke="#fff" stroke-width="1"/>
        <path d="M0,0 L-26.5,48.2 A55,55 0 0 1 -51.1,-20.2 Z" fill="var(--leaf-green)" stroke="#fff" stroke-width="1"/>
        <path d="M0,0 L-51.1,-20.2 A55,55 0 0 1 -29.5,-46.4 Z" fill="var(--amber)" stroke="#fff" stroke-width="1"/>
        <path d="M0,0 L-29.5,-46.4 A55,55 0 0 1 0,-55 Z" fill="var(--brand-blue)" stroke="#fff" stroke-width="1"/>
      </g>
      <g font-size="6.5" fill="#444" text-anchor="middle">
        <text x="238" y="172">1st Qtr</text><text x="238" y="180">58%</text>
        <text x="104" y="182">2nd Qtr</text><text x="104" y="190">23%</text>
        <text x="117" y="120">3rd Qtr</text><text x="117" y="128">10%</text>
        <text x="156" y="94">4th Qtr</text><text x="156" y="102">9%</text>
      </g>
    </svg>
    <div class="footer-band"><div class="brand-name"><span class="line-main">Meridian</span><span class="line-sub">Neuro-Care</span></div></div>
  </section>

  <!-- Bar chart -->
  <section class="slide col-3 row-2">
    <span class="title-dot"></span>
    <h2 class="slide-title">Bar Chart</h2>
    <svg class="chart" viewBox="0 0 335 255">
      <g font-size="5" fill="#555" text-anchor="end">
        <text x="64" y="192">0</text><text x="64" y="177">1</text><text x="64" y="162">2</text><text x="64" y="147">3</text>
        <text x="64" y="132">4</text><text x="64" y="117">5</text><text x="64" y="102">6</text><text x="64" y="87">7</text>
      </g>
      <line x1="68" y1="190" x2="268" y2="190" stroke="#999" stroke-width=".6"/>
      <line x1="68" y1="85" x2="68" y2="190" stroke="#999" stroke-width=".6"/>
      <g>
        <!-- A -->
        <rect x="76" y="125.5" width="8" height="64.5" fill="var(--brand-blue)"/>
        <rect x="85" y="154" width="8" height="36" fill="var(--leaf-green)"/>
        <rect x="94" y="160" width="8" height="30" fill="var(--amber)"/>
        <rect x="103" y="115" width="8" height="75" fill="var(--sky-blue)"/>
        <!-- B -->
        <rect x="126" y="152.5" width="8" height="37.5" fill="var(--brand-blue)"/>
        <rect x="135" y="124" width="8" height="66" fill="var(--leaf-green)"/>
        <rect x="144" y="145" width="8" height="45" fill="var(--amber)"/>
        <rect x="153" y="133" width="8" height="57" fill="var(--sky-blue)"/>
        <!-- C -->
        <rect x="176" y="137.5" width="8" height="52.5" fill="var(--brand-blue)"/>
        <rect x="185" y="163" width="8" height="27" fill="var(--leaf-green)"/>
        <rect x="194" y="100" width="8" height="90" fill="var(--amber)"/>
        <rect x="203" y="148" width="8" height="42" fill="var(--sky-blue)"/>
        <!-- D -->
        <rect x="226" y="122.5" width="8" height="67.5" fill="var(--brand-blue)"/>
        <rect x="235" y="148" width="8" height="42" fill="var(--leaf-green)"/>
        <rect x="244" y="115" width="8" height="75" fill="var(--amber)"/>
        <rect x="253" y="142" width="8" height="48" fill="var(--sky-blue)"/>
      </g>
      <g font-size="5" fill="#444" text-anchor="middle">
        <text x="80" y="123">4.3</text><text x="89" y="152">2.4</text><text x="98" y="158">2</text><text x="107" y="113">5</text>
        <text x="130" y="150">2.5</text><text x="139" y="122">4.4</text><text x="148" y="143">3</text><text x="157" y="131">3.8</text>
        <text x="180" y="135">3.5</text><text x="189" y="161">1.8</text><text x="198" y="98">6</text><text x="207" y="146">2.8</text>
        <text x="230" y="120">4.5</text><text x="239" y="146">2.8</text><text x="248" y="113">5</text><text x="257" y="140">3.2</text>
        <text x="93" y="200">A</text><text x="143" y="200">B</text><text x="193" y="200">C</text><text x="243" y="200">D</text>
      </g>
      <g font-size="5" fill="#444">
        <circle cx="278" cy="128" r="1.3" fill="var(--brand-blue)"/><text x="282" y="130">S1</text>
        <circle cx="278" cy="138" r="1.3" fill="var(--leaf-green)"/><text x="282" y="140">S2</text>
        <circle cx="278" cy="148" r="1.3" fill="var(--amber)"/><text x="282" y="150">S3</text>
        <circle cx="278" cy="158" r="1.3" fill="var(--sky-blue)"/><text x="282" y="160">S4</text>
      </g>
    </svg>
    <div class="footer-band"><div class="brand-name"><span class="line-main">Meridian</span><span class="line-sub">Neuro-Care</span></div></div>
  </section>

  <!-- Line chart -->
  <section class="slide col-1 row-3">
    <span class="title-dot"></span>
    <h2 class="slide-title">Line Chart</h2>
    <svg class="chart" viewBox="0 0 335 255">
      <g font-size="5" fill="#555" text-anchor="end">
        <text x="44" y="194">0</text><text x="44" y="181">0.5</text><text x="44" y="167">1</text><text x="44" y="154">1.5</text>
        <text x="44" y="140">2</text><text x="44" y="127">2.5</text><text x="44" y="113">3</text><text x="44" y="100">3.5</text>
        <text x="44" y="86">4</text><text x="44" y="73">4.5</text><text x="44" y="59">5</text>
      </g>
      <line x1="48" y1="192" x2="262" y2="192" stroke="#999" stroke-width=".6"/>
      <line x1="48" y1="57" x2="48" y2="192" stroke="#999" stroke-width=".6"/>
      <g fill="none" stroke-width="1.2">
        <polyline points="72,75.9 122,124.5 172,97.5 222,70.5" stroke="var(--amber)"/>
        <polyline points="72,127.2 122,73.2 172,143.4 222,116.4" stroke="var(--brand-navy)"/>
        <polyline points="72,165 122,159.6 172,121.8 222,151.5" stroke="var(--steel-blue)"/>
        <polyline points="72,181.2 122,100.2 172,70.5 222,92.1" stroke="var(--leaf-green)"/>
      </g>
      <g>
        <circle cx="72" cy="75.9" r="1.6" fill="var(--amber)"/><circle cx="122" cy="124.5" r="1.6" fill="var(--amber)"/><circle cx="172" cy="97.5" r="1.6" fill="var(--amber)"/><circle cx="222" cy="70.5" r="1.6" fill="var(--amber)"/>
        <circle cx="72" cy="127.2" r="1.6" fill="var(--brand-navy)"/><circle cx="122" cy="73.2" r="1.6" fill="var(--brand-navy)"/><circle cx="172" cy="143.4" r="1.6" fill="var(--brand-navy)"/><circle cx="222" cy="116.4" r="1.6" fill="var(--brand-navy)"/>
        <circle cx="72" cy="165" r="1.6" fill="var(--steel-blue)"/><circle cx="122" cy="159.6" r="1.6" fill="var(--steel-blue)"/><circle cx="172" cy="121.8" r="1.6" fill="var(--steel-blue)"/><circle cx="222" cy="151.5" r="1.6" fill="var(--steel-blue)"/>
        <circle cx="72" cy="181.2" r="1.6" fill="var(--leaf-green)"/><circle cx="122" cy="100.2" r="1.6" fill="var(--leaf-green)"/><circle cx="172" cy="70.5" r="1.6" fill="var(--leaf-green)"/><circle cx="222" cy="92.1" r="1.6" fill="var(--leaf-green)"/>
      </g>
      <g font-size="5" fill="#333" text-anchor="middle">
        <text x="72" y="71">4.3</text><text x="122" y="119">2.5</text><text x="172" y="92">3.5</text><text x="222" y="65">4.5</text>
        <text x="72" y="123">2.4</text><text x="122" y="68">4.4</text><text x="172" y="139">1.8</text><text x="222" y="112">2.8</text>
        <text x="72" y="160">1</text><text x="122" y="155">1.2</text><text x="172" y="117">2.6</text><text x="222" y="147">1.5</text>
        <text x="72" y="177" font-size="6" font-weight="700">0.4</text><text x="122" y="96" font-size="6" font-weight="700">3.4</text><text x="172" y="66" font-size="6" font-weight="700">4.5</text><text x="222" y="88" font-size="6" font-weight="700">3.7</text>
        <text x="72" y="202">Category 1</text><text x="122" y="202">Category 2</text><text x="172" y="202">Category 3</text><text x="222" y="202">Category 4</text>
      </g>
      <g font-size="4.5" fill="#444">
        <rect x="258" y="137" width="4" height="2" fill="var(--amber)"/><text x="265" y="140">Series 1</text>
        <rect x="258" y="145" width="4" height="2" fill="var(--brand-navy)"/><text x="265" y="148">Series 2</text>
        <rect x="258" y="153" width="4" height="2" fill="var(--steel-blue)"/><text x="265" y="156">Series 3</text>
        <rect x="258" y="161" width="4" height="2" fill="var(--leaf-green)"/><text x="265" y="164">Series 4</text>
      </g>
    </svg>
    <div class="footer-band"><div class="brand-name"><span class="line-main">Meridian</span><span class="line-sub">Neuro-Care</span></div></div>
  </section>

  <!-- Table -->
  <section class="slide col-2 row-3">
    <span class="title-dot"></span>
    <h2 class="slide-title">Table</h2>
    <table class="data-table">
      <thead><tr><th>Title A</th><th>Title B</th><th>Title C</th><th>Title D</th><th>Title E</th></tr></thead>
      <tbody>
        <tr><td>Text here</td><td>1234567890</td><td>1234567890</td><td>1234567890</td><td>1234567890</td></tr>
        <tr><td>Text here</td><td>1234567890</td><td>1234567890</td><td>1234567890</td><td>1234567890</td></tr>
        <tr><td>Text here</td><td>1234567890</td><td>1234567890</td><td>1234567890</td><td>1234567890</td></tr>
        <tr><td>Text here</td><td>1234567890</td><td>1234567890</td><td>1234567890</td><td>1234567890</td></tr>
        <tr><td>Text here</td><td>1234567890</td><td>1234567890</td><td>1234567890</td><td>1234567890</td></tr>
        <tr><td>Text here</td><td>1234567890</td><td>1234567890</td><td>1234567890</td><td>1234567890</td></tr>
        <tr><td>Text here</td><td>1234567890</td><td>1234567890</td><td>1234567890</td><td>1234567890</td></tr>
        <tr><td>Text here</td><td>1234567890</td><td>1234567890</td><td>1234567890</td><td>1234567890</td></tr>
      </tbody>
    </table>
    <div class="footer-band"><div class="brand-name"><span class="line-main">Meridian</span><span class="line-sub">Neuro-Care</span></div></div>
  </section>

  <!-- Closing -->
  <section class="slide slide--feature cover col-3 row-3">
    <div class="dot-field" role="img" aria-label="Scattered dots in blue, green and amber"></div>
    <div class="brand-name"><span class="line-main">Meridian</span><span class="line-sub">Neuro-Care</span></div>
    <p class="cover-heading" style="top:178px">Thank You</p>
    <p class="cover-date" style="top:200px">October 26, 2013</p>
  </section>
</body>
</html>
```